RW Framewell Inc Business cards

We need business cards using our existing logo but slightly modified. Right now the logo says RW Loadbearing Masonry. We want to keep the RW part of the design, but replace the Structural Concrete portion with "FRAMEWELL". Please see the attached file.
Ideally this would be a blank template so we can add Different Names, titles, and phone numbers later.
On the one side we want only the logo and on the other side the detail. I'm attaching an example for you to see.
Please reach out with any other questions. Our address and other details will be given out once we find a design we like.

Target Market(s)

Construction Industry

```html
<!DOCTYPE html>
<html lang="en">
<head>
<meta charset="utf-8">
<title>RW Framewell Inc – Business Cards</title>
<link href="https://fonts.googleapis.com/css2?family=Roboto:wght@400;500;700&display=swap" rel="stylesheet">
<style>
  :root {
    --brand-blue: #0f77c0;
    --ink: #2f2f33;
    --rule-gray: #8a8a8e;
    --band-gray: #88898d;
    --paper: #ffffff;
    --backdrop: #9b9b9b;
  }
  * { box-sizing: border-box; margin: 0; padding: 0; }
  html, body {
    width: 1021px; height: 1200px; overflow: hidden;
    background: var(--backdrop);
    font-family: "Roboto", Arial, sans-serif;
  }
  .canvas { position: relative; width: 1021px; height: 1200px; }

  .card { position: absolute; width: 753px; height: 429px; overflow: hidden; }

  /* Front side */
  .card--front { left: 134px; top: 119px; background: var(--brand-blue); }
  .front-mark {
    position: absolute; left: 531px; top: 300px; width: 127px;
    color: var(--paper); font-weight: 700; text-align: center;
  }
  .front-mark__initials { font-size: 66px; line-height: 1; letter-spacing: 2px; }
  .front-mark__name {
    margin-top: 6px; font-size: 10px; letter-spacing: 7.2px; margin-right: -7px;
  }

  /* Back side */
  .card--back { left: 131px; top: 650px; background: var(--paper); }
  .back-mark {
    position: absolute; left: 34px; top: 64px;
    font-size: 108px; font-weight: 700; line-height: 1;
    color: var(--brand-blue); letter-spacing: 2px;
  }
  .person { position: absolute; right: 38px; top: 216px; text-align: right; }
  .person__name {
    font-size: 28px; font-weight: 700; color: var(--brand-blue); line-height: 1;
  }
  .divider {
    position: absolute; left: 36px; top: 258px; width: 581px; height: 1.5px;
    background: var(--rule-gray);
  }
  .person__title {
    position: absolute; right: 38px; top: 248px;
    font-size: 18px; color: var(--ink); line-height: 1;
  }
  .contacts { position: absolute; left: 36px; top: 276px; list-style: none; }
  .contacts li {
    display: flex; align-items: center; height: 24px;
    font-size: 18px; color: var(--ink);
  }
  .contacts svg { width: 14px; height: 14px; margin-right: 6px; fill: var(--brand-blue); flex: none; }

  .footer-band { position: absolute; left: 0; bottom: 0; width: 753px; height: 46px; }
  .address {
    position: absolute; left: 37px; bottom: 11px;
    font-size: 18px; color: var(--paper); line-height: 1;
  }
</style>
</head>
<body>
<main class="canvas">

  <section class="card card--front" aria-label="Card front">
    <div class="front-mark">
      <div class="front-mark__initials">RW</div>
      <div class="front-mark__name">FRAMEWELL</div>
    </div>
  </section>

  <section class="card card--back" aria-label="Card back">
    <div class="back-mark">RW</div>

    <div class="person">
      <div class="person__name">DANA MERCER</div>
    </div>
    <div class="divider"></div>
    <div class="person__title">Owner/CEO</div>

    <ul class="contacts">
      <li>
        <svg viewBox="0 0 14 14" aria-hidden="true"><path d="M4 0h6a1.5 1.5 0 0 1 1.5 1.5v11A1.5 1.5 0 0 1 10 14H4a1.5 1.5 0 0 1-1.5-1.5v-11A1.5 1.5 0 0 1 4 0zm0 2v9h6V2zm3 9.6a.9.9 0 1 0 0 1.8.9.9 0 0 0 0-1.8z"/></svg>
        555-014-2278
      </li>
      <li>
        <svg viewBox="0 0 14 14" aria-hidden="true"><path d="M3 1l2.2 2.8-1.2 1.6a7.5 7.5 0 0 0 4.6 4.6l1.6-1.2L13 11l-1.6 2c-5.5 0-10.4-4.9-10.4-10.4z"/></svg>
        555-019-6643
      </li>
      <li>
        <svg viewBox="0 0 14 14" aria-hidden="true"><path d="M0 3h14v8H0zm1.3 1.2v.4L7 8.2l5.7-3.6v-.4zM1.3 6v3.8h11.4V6L7 9.6z"/></svg>
        info@rwframewell.com
      </li>
      <li>
        <svg viewBox="0 0 14 14" aria-hidden="true"><path d="M7 0a7 7 0 1 0 0 14A7 7 0 0 0 7 0zm-1 2.2l1.8 1.4-.6 1.6L5 5.8 4.2 8l1.6 1.2-.6 2.5A5.3 5.3 0 0 1 3 2.8zm4.2 1.5l1.5 2.5-1.6 1.5-1.7-.8.4-2z"/></svg>
        www.rwframewell.com
      </li>
    </ul>

    <svg class="footer-band" viewBox="0 0 753 46" preserveAspectRatio="none" aria-hidden="true">
      <polygon points="443,36 753,36 753,46 450,46" fill="var(--band-gray)"/>
      <polygon points="0,0 431,0 463,46 0,46" fill="var(--brand-blue)"/>
    </svg>
    <div class="address">1450 W Harlan Avenue County Name 6120</div>
  </section>

</main>
</body>
</html>
```